RESINE DENTAIRE ROSE box for dental resine pink to repair dentures broken

I will need a design for a box of pink dental resin. It is a pink dental resin which is intended for sale to individuals on Brindleway to repair or make small touch-ups or modifications to their dental prostheses. The title RESINE DENTAIRE ROSE must be clearly visible as well as the company logo. .I leave it to your creative mind to make an attractive and highly impactful and clearly visible sales design.
It is also necessary to make it clear to buyers through text or a vector image the purpose of the product: to repair a dental prosthesis.
Faible participation designers
Particulars who have need to repair their dentures

```html
<!DOCTYPE html>
<html lang="fr">
<head>
<meta charset="utf-8">
<title>Résine Dentaire Rose – Packaging</title>
<link rel="stylesheet" href="https://fonts.googleapis.com/css2?family=Montserrat:wght@400;500;600;700;800&display=swap">
<style>
  :root {
    --pink: #ea1468;
    --pink-light: #ef3a82;
    --pink-title: #e6307a;
    --silver-light: #f3f3f4;
    --silver: #d4d5d7;
    --silver-dark: #a9aaad;
    --ink: #333336;
    --green: #7ab52f;
    --green-dark: #4d8e33;
    --white: #ffffff;
    --stage: #eceef1;
  }
  * { margin: 0; padding: 0; box-sizing: border-box; }
  html, body { width: 1200px; height: 2662px; overflow: hidden; background: var(--white); }
  body { position: relative; font-family: "Montserrat", sans-serif; }

  .sheet { position: absolute; left: 0; top: 0; width: 1200px; height: 2662px; border: 1px solid #dcdcdc; }

  /* ---------- front panel (designed at 762 x 914) ---------- */
  .front-holder { position: absolute; transform-origin: 0 0; }
  .front { position: relative; width: 762px; height: 914px; overflow: hidden; }
  .front-bg { position: absolute; inset: 0; }
  .brand { position: absolute; top: 78px; left: 0; width: 100%; display: flex; justify-content: center; align-items: center; gap: 16px; }
  .brand-square { width: 58px; height: 58px; background: var(--green); border-radius: 4px; }
  .brand-name { font-weight: 600; font-size: 32px; line-height: 1.05; color: var(--green-dark); letter-spacing: 2px; }
  .brand-since { font-weight: 600; font-size: 12px; color: var(--green-dark); text-align: center; margin-left: 4px; align-self: flex-end; }
  .brand-since b { display: block; font-size: 20px; font-weight: 600; }
  .title { position: absolute; top: 290px; width: 100%; text-align: center; font-weight: 700; font-size: 60px; line-height: 78px; color: var(--pink-title); letter-spacing: 0.5px; }
  .subtitle { position: absolute; top: 475px; width: 100%; text-align: center; font-weight: 500; font-size: 25px; line-height: 32px; color: var(--ink); }
  .seal { position: absolute; left: 321px; top: 570px; width: 120px; height: 140px; }
  .feature-badge { position: absolute; z-index: 1; border-radius: 50%; border: 4px solid var(--white); box-shadow: 0 4px 10px rgba(0,0,0,.35); background: radial-gradient(circle at 40% 35%, #f8c6d8, var(--pink) 75%); }
  .feature-label { position: absolute; z-index: 2; color: var(--white); font-weight: 700; font-size: 14px; line-height: 18px; text-align: center; white-space: nowrap; transform: translateX(-50%); }

  .stage { position: absolute; left: 0; top: 1109px; width: 1200px; height: 840px; background: var(--stage); }

  .dieline { position: absolute; left: 0; top: 0; }
  .side-copy { position: absolute; color: var(--white); font-size: 6px; line-height: 8px; transform: rotate(90deg); transform-origin: 0 0; }
  .side-copy.dark { color: #3b1a28; }
</style>
</head>
<body>
<main class="sheet">

  <!-- flat front panel -->
  <div class="front-holder" style="left:219px; top:100px;">
    <section class="front">
      <svg class="front-bg" viewBox="0 0 762 914" aria-hidden="true">
        <defs>
          <linearGradient id="pinkFill" x1="0" y1="0" x2="0" y2="1"><stop offset="0" stop-color="#e60f64"/><stop offset="1" stop-color="#ee2b7b"/></linearGradient>
          <linearGradient id="silverFill" x1="0" y1="0" x2="1" y2="0"><stop offset="0" stop-color="#c9cacc"/><stop offset=".5" stop-color="#f6f6f7"/><stop offset="1" stop-color="#c6c7c9"/></linearGradient>
        </defs>
        <rect width="762" height="914" fill="url(#pinkFill)"/>
        <path d="M0,0H762V190C762,500 600,690 381,775 C162,690 0,500 0,190Z" fill="#9d9ea1"/>
        <path d="M0,0H762V190C762,490 595,670 381,750 C167,670 0,490 0,190Z" fill="url(#silverFill)"/>
      </svg>
      <div class="brand"><span class="brand-square"></span><span class="brand-name">LABORATOIRE<br>ORVANE</span><span class="brand-since">Depuis<b>1990</b></span></div>
      <h1 class="title">RESINE DENTAIRE<br>ROSE</h1>
      <p class="subtitle">REPAIR<br>DENTAL PROSTHESIS</p>
      <svg class="seal" viewBox="0 0 120 140" aria-label="Bouclier avec coche">
        <path d="M60,4 L114,30 V78 C114,108 88,128 60,138 C32,128 6,108 6,78 V30Z" fill="#f7c9d9"/>
        <path d="M60,12 L106,35 V78 C106,104 84,121 60,130 C36,121 14,104 14,78 V35Z" fill="#ea2c74"/>
        <path d="M36,70 L54,88 L86,54" fill="none" stroke="#fde6ef" stroke-width="12" stroke-linecap="round" stroke-linejoin="round"/>
      </svg>
      <div class="feature-badge" role="img" aria-label="Illustration d'une main facile à utiliser" style="left:66px; top:526px; width:90px; height:90px;"></div>
      <div class="feature-label" style="left:100px; top:620px;">FACILITÉ D'EMPLOI</div>
      <div class="feature-badge" role="img" aria-label="Illustration d'un dentier réparé" style="left:160px; top:642px; width:124px; height:124px;"></div>
      <div class="feature-label" style="left:222px; top:776px;">PETITES RÉPARATIONS</div>
      <div class="feature-badge" role="img" aria-label="Illustration d'un dentier avec une dent détachée" style="left:478px; top:642px; width:124px; height:124px;"></div>
      <div class="feature-label" style="left:540px; top:776px;">DENT DÉTACHÉE</div>
      <div class="feature-badge" role="img" aria-label="Illustration d'un chronomètre" style="left:606px; top:526px; width:90px; height:90px;"></div>
      <div class="feature-label" style="left:656px; top:620px;">EN 10 MINUTES</div>
    </section>
  </div>

  <!-- plain presentation area with the front panel -->
  <div class="stage"></div>
  <div class="front-holder" style="left:425px; top:1320px; transform:scale(.46);">
    <section class="front">
      <svg class="front-bg" viewBox="0 0 762 914" aria-hidden="true">
        <rect width="762" height="914" fill="url(#pinkFill)"/>
        <path d="M0,0H762V190C762,500 600,690 381,775 C162,690 0,500 0,190Z" fill="#9d9ea1"/>
        <path d="M0,0H762V190C762,490 595,670 381,750 C167,670 0,490 0,190Z" fill="url(#silverFill)"/>
      </svg>
      <div class="brand"><span class="brand-square"></span><span class="brand-name">LABORATOIRE<br>ORVANE</span><span class="brand-since">Depuis<b>1990</b></span></div>
      <h2 class="title">RESINE DENTAIRE<br>ROSE</h2>
      <p class="subtitle">REPAIR<br>DENTAL PROSTHESIS</p>
      <svg class="seal" viewBox="0 0 120 140" aria-label="Bouclier avec coche">
        <path d="M60,4 L114,30 V78 C114,108 88,128 60,138 C32,128 6,108 6,78 V30Z" fill="#f7c9d9"/>
        <path d="M60,12 L106,35 V78 C106,104 84,121 60,130 C36,121 14,104 14,78 V35Z" fill="#ea2c74"/>
        <path d="M36,70 L54,88 L86,54" fill="none" stroke="#fde6ef" stroke-width="12" stroke-linecap="round" stroke-linejoin="round"/>
      </svg>
      <div class="feature-badge" role="img" aria-label="Illustration d'une main facile à utiliser" style="left:66px; top:526px; width:90px; height:90px;"></div>
      <div class="feature-label" style="left:100px; top:620px;">FACILITÉ D'EMPLOI</div>
      <div class="feature-badge" role="img" aria-label="Illustration d'un dentier réparé" style="left:160px; top:642px; width:124px; height:124px;"></div>
      <div class="feature-label" style="left:222px; top:776px;">PETITES RÉPARATIONS</div>
      <div class="feature-badge" role="img" aria-label="Illustration d'un dentier avec une dent détachée" style="left:478px; top:642px; width:124px; height:124px;"></div>
      <div class="feature-label" style="left:540px; top:776px;">DENT DÉTACHÉE</div>
      <div class="feature-badge" role="img" aria-label="Illustration d'un chronomètre" style="left:606px; top:526px; width:90px; height:90px;"></div>
      <div class="feature-label" style="left:656px; top:620px;">EN 10 MINUTES</div>
    </section>
  </div>

  <!-- dieline -->
  <svg class="dieline" width="1200" height="2662" viewBox="0 0 1200 2662" aria-label="Gabarit de découpe de la boîte">
    <g fill="#ea1468">
      <path d="M278,2190 L320,2180 V2435 L278,2425Z"/>
      <path d="M320,2180 V2062 Q320,2040 342,2040 H510 Q532,2040 532,2062 V2180Z"/>
      <path d="M532,2180 L545,2110 H605 L622,2180Z"/>
      <rect x="532" y="2180" width="90" height="255"/>
      <path d="M532,2435 L545,2505 H605 L622,2435Z"/>
      <path d="M833,2180 L848,2110 H908 L922,2180Z"/>
      <rect x="833" y="2180" width="89" height="255"/>
      <path d="M833,2435 L848,2505 H908 L922,2435Z"/>
      <path d="M622,2435 V2543 Q622,2565 644,2565 H811 Q833,2565 833,2543 V2435Z"/>
    </g>
  </svg>
  <div class="side-copy" style="left:598px; top:2190px; width:230px;">AVERTISSEMENT : tenir hors de portée des enfants. Usage externe uniquement. Bien refermer après usage.</div>
  <div class="side-copy" style="left:560px; top:2190px; width:230px;">Distribué par Laboratoire Orvane. Conserver à l'abri de la chaleur et de la lumière.</div>
  <div class="side-copy dark" style="left:870px; top:2240px; width:150px;">Monomère : Méthacrylate de méthyle<br>Poudre : Polyméthylméthacrylate<br>LOT :</div>

  <div class="front-holder" style="left:320px; top:2180px; transform:scale(.278);">
    <section class="front">
      <svg class="front-bg" viewBox="0 0 762 914" aria-hidden="true">
        <rect width="762" height="914" fill="url(#pinkFill)"/>
        <path d="M0,0H762V190C762,500 600,690 381,775 C162,690 0,500 0,190Z" fill="#9d9ea1"/>
        <path d="M0,0H762V190C762,490 595,670 381,750 C167,670 0,490 0,190Z" fill="url(#silverFill)"/>
      </svg>
      <div class="brand"><span class="brand-square"></span><span class="brand-name">LABORATOIRE<br>ORVANE</span><span class="brand-since">Depuis<b>1990</b></span></div>
      <h2 class="title">RESINE DENTAIRE<br>ROSE</h2>
      <p class="subtitle">REPAIR<br>DENTAL PROSTHESIS</p>
      <svg class="seal" viewBox="0 0 120 140" aria-label="Bouclier avec coche">
        <path d="M60,4 L114,30 V78 C114,108 88,128 60,138 C32,128 6,108 6,78 V30Z" fill="#f7c9d9"/>
        <path d="M60,12 L106,35 V78 C106,104 84,121 60,130 C36,121 14,104 14,78 V35Z" fill="#ea2c74"/>
        <path d="M36,70 L54,88 L86,54" fill="none" stroke="#fde6ef" stroke-width="12" stroke-linecap="round" stroke-linejoin="round"/>
      </svg>
      <div class="feature-badge" role="img" aria-label="Illustration d'une main" style="left:66px; top:526px; width:90px; height:90px;"></div>
      <div class="feature-label" style="left:100px; top:620px;">FACILITÉ D'EMPLOI</div>
      <div class="feature-badge" role="img" aria-label="Illustration d'un dentier réparé" style="left:160px; top:642px; width:124px; height:124px;"></div>
      <div class="feature-label" style="left:222px; top:776px;">PETITES RÉPARATIONS</div>
      <div class="feature-badge" role="img" aria-label="Illustration d'une dent détachée" style="left:478px; top:642px; width:124px; height:124px;"></div>
      <div class="feature-label" style="left:540px; top:776px;">DENT DÉTACHÉE</div>
      <div class="feature-badge" role="img" aria-label="Illustration d'un chronomètre" style="left:606px; top:526px; width:90px; height:90px;"></div>
      <div class="feature-label" style="left:656px; top:620px;">EN 10 MINUTES</div>
    </section>
  </div>

  <div class="front-holder" style="left:622px; top:2180px; transform:scale(.278);">
    <section class="front">
      <svg class="front-bg" viewBox="0 0 762 914" aria-hidden="true">
        <rect width="762" height="914" fill="url(#pinkFill)"/>
        <path d="M0,0H762V190C762,500 600,690 381,775 C162,690 0,500 0,190Z" fill="#9d9ea1"/>
        <path d="M0,0H762V190C762,490 595,670 381,750 C167,670 0,490 0,190Z" fill="url(#silverFill)"/>
      </svg>
      <div class="brand"><span class="brand-square"></span><span class="brand-name">LABORATOIRE<br>ORVANE</span><span class="brand-since">Depuis<b>1990</b></span></div>
      <h2 class="title">RESINE DENTAIRE<br>ROSE</h2>
      <p class="subtitle">REPAIR<br>DENTAL PROSTHESIS</p>
      <svg class="seal" viewBox="0 0 120 140" aria-label="Bouclier avec coche">
        <path d="M60,4 L114,30 V78 C114,108 88,128 60,138 C32,128 6,108 6,78 V30Z" fill="#f7c9d9"/>
        <path d="M60,12 L106,35 V78 C106,104 84,121 60,130 C36,121 14,104 14,78 V35Z" fill="#ea2c74"/>
        <path d="M36,70 L54,88 L86,54" fill="none" stroke="#fde6ef" stroke-width="12" stroke-linecap="round" stroke-linejoin="round"/>
      </svg>
      <div class="feature-badge" role="img" aria-label="Illustration d'une main" style="left:66px; top:526px; width:90px; height:90px;"></div>
      <div class="feature-label" style="left:100px; top:620px;">FACILITÉ D'EMPLOI</div>
      <div class="feature-badge" role="img" aria-label="Illustration d'un dentier réparé" style="left:160px; top:642px; width:124px; height:124px;"></div>
      <div class="feature-label" style="left:222px; top:776px;">PETITES RÉPARATIONS</div>
      <div class="feature-badge" role="img" aria-label="Illustration d'une dent détachée" style="left:478px; top:642px; width:124px; height:124px;"></div>
      <div class="feature-label" style="left:540px; top:776px;">DENT DÉTACHÉE</div>
      <div class="feature-badge" role="img" aria-label="Illustration d'un chronomètre" style="left:606px; top:526px; width:90px; height:90px;"></div>
      <div class="feature-label" style="left:656px; top:620px;">EN 10 MINUTES</div>
    </section>
  </div>

</main>
</body>
</html>
```